SaaS Early tech startup business card design

Unique design for experience ecommerce platform company. the business cards will be used by executive members. conformance with color code is required.

```html
<!DOCTYPE html>
<html lang="en">
<head>
<meta charset="utf-8">
<title>Novaro business card</title>
<link rel="stylesheet" href="https://fonts.googleapis.com/css2?family=Lexend:wght@600;700&family=Montserrat:wght@500&family=Roboto:wght@400&display=swap">
<style>
  :root {
    --backdrop: #6b6868;
    --navy: #1f2035;
    --teal: #1fa99a;
    --teal-deep: #127a82;
    --grad-start: #0a9a8f;
    --grad-end: #0f5a86;
    --edge-band: #0c6e78;
    --paper: #f4f5f5;
    --ink: #2a2a2a;
    --white: #ffffff;
  }
  html, body {
    margin: 0;
    width: 1200px;
    height: 1200px;
    overflow: hidden;
    background: var(--backdrop);
  }
  .canvas {
    position: relative;
    width: 1200px;
    height: 1200px;
  }
  .card {
    position: absolute;
    width: 592px;
    height: 348px;
    border-radius: 26px;
    overflow: hidden;
  }
  .card--front {
    left: 300px;
    top: 198px;
    background: var(--navy);
  }
  .card--back {
    left: 292px;
    top: 637px;
    background: var(--paper);
  }
  .wordmark {
    position: absolute;
    left: 0;
    width: 100%;
    text-align: center;
    margin: 0;
    font-family: "Lexend", sans-serif;
    font-weight: 700;
    line-height: 1;
    letter-spacing: -0.01em;
  }
  .card--front .wordmark {
    top: 112px;
    font-size: 84px;
    color: var(--teal);
  }
  .tagline {
    position: absolute;
    margin: 0;
    font-family: "Montserrat", sans-serif;
    font-weight: 500;
    letter-spacing: 0.36em;
    white-space: nowrap;
  }
  .card--front .tagline {
    left: 0;
    width: 100%;
    text-align: center;
    top: 206px;
    font-size: 17px;
    color: var(--white);
    padding-left: 0.36em;
    box-sizing: border-box;
  }
  .back-panel {
    position: absolute;
    left: 0;
    top: 0;
  }
  .back-brand {
    position: absolute;
    left: 0;
    top: 0;
    width: 304px;
    height: 348px;
  }
  .card--back .wordmark {
    top: 122px;
    font-size: 72px;
    color: var(--white);
  }
  .card--back .tagline {
    left: 0;
    width: 100%;
    text-align: center;
    top: 203px;
    font-size: 14px;
    color: var(--white);
    padding-left: 0.36em;
    box-sizing: border-box;
  }
  .contact {
    position: absolute;
    left: 360px;
    top: 80px;
    font-family: "Roboto", sans-serif;
    color: var(--ink);
  }
  .contact__name {
    margin: 0;
    font-family: "Lexend", sans-serif;
    font-weight: 600;
    font-size: 24px;
    line-height: 1.1;
    color: var(--teal-deep);
    letter-spacing: -0.01em;
  }
  .contact__role {
    margin: 4px 0 0;
    font-size: 15.5px;
  }
  .contact__list {
    list-style: none;
    margin: 24px 0 0;
    padding: 0;
  }
  .contact__item {
    display: flex;
    align-items: center;
    height: 22.5px;
    font-size: 15.5px;
  }
  .contact__icon {
    width: 14px;
    height: 14px;
    margin: 0 16px 0 1px;
    flex: none;
  }
  .contact__address {
    margin: 10px 0 0;
    font-style: normal;
    font-size: 15.5px;
    line-height: 22.5px;
  }
</style>
</head>
<body>
<main class="canvas">

  <section class="card card--front" aria-label="Card front">
    <h1 class="wordmark">novaro</h1>
    <p class="tagline">MADE AROUND YOU</p>
  </section>

  <section class="card card--back" aria-label="Card back">
    <svg class="back-panel" width="592" height="348" viewBox="0 0 592 348" aria-hidden="true">
      <defs>
        <linearGradient id="brandGradient" x1="0" y1="0" x2="1" y2="1">
          <stop offset="0" stop-color="var(--grad-start)"/>
          <stop offset="1" stop-color="var(--grad-end)"/>
        </linearGradient>
      </defs>
      <path d="M0 0 H282 Q384 174 274 348 H0 Z" fill="var(--edge-band)"/>
      <path d="M0 0 H262 Q362 174 258 348 H0 Z" fill="url(#brandGradient)"/>
    </svg>

    <div class="back-brand">
      <h2 class="wordmark">novaro</h2>
      <p class="tagline">MADE AROUND YOU</p>
    </div>

    <div class="contact">
      <p class="contact__name">Idris K.</p>
      <p class="contact__role">CTO/Owner</p>
      <ul class="contact__list">
        <li class="contact__item">
          <svg class="contact__icon" viewBox="0 0 16 16" aria-hidden="true">
            <path d="M1 5 Q8 0 15 5 L13 7 L11 5.5 L5 5.5 L3 7 Z" fill="var(--teal-deep)"/>
            <rect x="3" y="7.5" width="10" height="7" rx="1.5" fill="var(--teal-deep)"/>
            <circle cx="8" cy="11" r="1.8" fill="var(--paper)"/>
          </svg>
          (00) 0111 NOVA
        </li>
        <li class="contact__item">
          <svg class="contact__icon" viewBox="0 0 16 16" aria-hidden="true">
            <rect x="1" y="3" width="14" height="10" fill="var(--teal-deep)"/>
            <path d="M1.5 3.5 L8 9 L14.5 3.5 M1.5 12.5 L6 7.5 M14.5 12.5 L10 7.5" stroke="var(--paper)" stroke-width="1.2" fill="none"/>
          </svg>
          info@novaro.net
        </li>
        <li class="contact__item">
          <svg class="contact__icon" viewBox="0 0 16 16" aria-hidden="true">
            <circle cx="8" cy="8" r="6.5" fill="var(--teal-deep)"/>
            <path d="M1.5 8 H14.5 M8 1.5 V14.5 M2.8 4.8 H13.2 M2.8 11.2 H13.2" stroke="var(--paper)" stroke-width="0.9" fill="none"/>
            <ellipse cx="8" cy="8" rx="3" ry="6.5" stroke="var(--paper)" stroke-width="0.9" fill="none"/>
          </svg>
          www.novaro.net
        </li>
      </ul>
      <address class="contact__address">
        Harbor Tower, Dubai<br>
        Marina Tech District, UAE
      </address>
    </div>
  </section>

</main>
</body>
</html>
```